I need a fresh looking, exciting and loaded design for Full service Restaurant

We need a web design for our restaurant, which offers full service Pakistani and Indian food in PA, USA. Design should be elegant, simplified so customers can navigate easily and order food online for catering as well as delivery. We need loads of pictures and room to grow. I already have a web address via vemrilo.com. It should include SSL and e-commerce for ordering food.
Be original and be creative and make it a fun site :)

```html
<!DOCTYPE html>
<html lang="en">
<head>
<meta charset="utf-8">
<title>Saffron Lane – Pakistani and Indian food</title>
<link href="https://fonts.googleapis.com/css2?family=Open+Sans:wght@400;600;700&family=Great+Vibes&display=swap" rel="stylesheet">
<style>
:root{
  --green:#2d6b0e;
  --green-dark:#1d4808;
  --green-deep:#173a06;
  --red:#c0151a;
  --red-dark:#a30d12;
  --paper:#f1f0ec;
  --white:#ffffff;
  --ink:#333333;
  --muted:#555555;
  --line:#d8d8d4;
  --footer-text:#b9cfa8;
}
*{box-sizing:border-box;margin:0;padding:0}
html,body{width:1200px;height:2439px;overflow:hidden}
body{position:relative;background:var(--paper);font-family:"Open Sans",Arial,sans-serif;color:var(--ink)}
.abs{position:absolute}
.script{font-family:"Great Vibes",cursive;font-weight:400}

/* header + hero */
.hero{left:0;top:0;width:1200px;height:568px;background:radial-gradient(ellipse at 40% 45%,#b8621e 0%,#7a3512 35%,#3a1c0c 70%,#1e120a 100%)}
.topbar{left:0;top:0;width:1200px;height:135px;background:rgba(235,232,226,.82)}
.brand{left:134px;top:40px;display:flex;align-items:center;gap:12px;font-size:34px;font-weight:700;color:var(--red)}
.brand i{width:46px;height:46px;border-radius:50%;background:var(--green);display:block}
.contact-top{top:20px;display:flex;align-items:center;gap:12px;font-size:13px;font-weight:600;color:#444}
.contact-top span.ic{width:34px;height:34px;border-radius:50%;background:var(--green);display:flex;align-items:center;justify-content:center}
.nav{left:458px;top:88px;display:flex;font-size:12px;font-weight:600;letter-spacing:.5px;color:#333}
.nav a{color:inherit;text-decoration:none;margin-right:35px;position:relative}
.nav a.active{color:var(--red)}
.nav a.active::after{content:"";position:absolute;left:-2px;right:-2px;top:36px;height:5px;background:var(--red)}
.hero-title{left:0;width:1200px;top:306px;text-align:center;font-size:40px;font-weight:700;color:var(--white)}
.btn{background:var(--red);color:var(--white);font-size:13px;font-weight:700;display:flex;align-items:center;justify-content:center;border-radius:3px}
.hero-btn{left:531px;top:391px;width:137px;height:46px}
.arrow{top:324px;width:30px;height:30px;border-radius:50%;background:rgba(0,0,0,.35)}

/* welcome */
.section-title{left:0;width:1200px;text-align:center;font-size:54px;color:var(--red)}
.section-sub{left:0;width:1200px;text-align:center;font-size:13px;letter-spacing:1.5px;color:var(--green)}
.feature{top:718px;width:298px;height:171px;background:var(--paper);border:1px solid var(--line);padding:30px 18px 30px 28px}
.feature h3{font-size:19px;font-weight:600;color:var(--green-dark);display:flex;align-items:center;gap:14px}
.feature p{margin:12px 0 0 50px;font-size:11.5px;line-height:22px;color:var(--muted)}

/* specials */
.specials{left:0;top:945px;width:1200px;height:542px;background:linear-gradient(var(--green) 0%,var(--green-dark) 100%)}
.card{top:1107px;width:219px;height:321px;background:var(--white)}
.card .photo{height:172px}
.card h4{margin:12px 16px 0;font-size:19px;font-weight:400;line-height:29px;color:var(--green-dark)}
.card .btn{position:absolute;left:16px;top:256px;width:82px;height:38px;font-size:11px;font-weight:400}

/* testimonials + blog */
.quote-box{left:132px;top:1640px;width:458px;height:248px;border:1px solid var(--line)}
.avatar{left:162px;top:1684px;width:88px;height:88px;border-radius:50%;background:linear-gradient(#5a4a40,#b08a70)}
.quote{left:272px;top:1686px;width:290px;font-size:12px;line-height:23px;color:#444}
.post-photo{left:624px;width:117px;height:107px;border:4px solid var(--white);box-shadow:0 0 0 1px var(--line)}
.post{left:765px;width:310px}
.post h5{font-size:19px;font-weight:600;color:var(--green-deep)}
.post .date{font-size:12px;color:var(--red);margin-top:4px}
.post p{font-size:12px;line-height:22px;color:#444;margin-top:6px}

/* newsletter */
.newsletter{left:0;top:1948px;width:1200px;height:140px;background:linear-gradient(var(--red) 0%,var(--red-dark) 100%)}
.mail-input{left:667px;top:1999px;width:225px;height:48px;background:var(--white);border-radius:3px;font-size:11px;color:#666;display:flex;align-items:center;gap:10px;padding-left:20px}
.subscribe{left:909px;top:1999px;width:122px;height:48px;background:#111;color:var(--white);font-size:14px;display:flex;align-items:center;justify-content:center;border-radius:3px}

/* footer */
.footer{left:0;top:2088px;width:1200px;height:277px;background:var(--green-dark)}
.footer-bottom{left:0;top:2365px;width:1200px;height:74px;background:var(--green-deep);text-align:center;font-size:11px;color:#7b9a67;padding-top:21px}
.fcol h6{font-size:20px;font-weight:400;color:var(--white);margin-bottom:22px}
.fcol li{list-style:none;font-size:12px;line-height:22px;color:var(--footer-text)}
.fcol li.ic{padding-left:20px;position:relative}
.fcol li.ic svg{position:absolute;left:0;top:5px}
.hours td{font-size:12px;line-height:22px;color:var(--footer-text);padding-right:14px}
.social{top:2236px;width:46px;height:46px;border-radius:50%;background:var(--green-deep);display:flex;align-items:center;justify-content:center}
.footer-brand{left:797px;top:2140px;font-size:34px;font-weight:700;color:#2a5a12}
</style>
</head>
<body>

<!-- hero -->
<div class="abs hero" role="img" aria-label="Photo of pots of curries and dishes at a food counter"></div>
<div class="abs topbar"></div>
<div class="abs brand"><i></i>Saffron Lane</div>
<div class="abs contact-top" style="left:718px"><span class="ic"><svg width="14" height="14" viewBox="0 0 24 24"><path fill="#fff" d="M6.6 10.8a15 15 0 006.6 6.6l2.2-2.2a1 1 0 011-.3 11 11 0 003.6.6 1 1 0 011 1V20a1 1 0 01-1 1A17 17 0 013 4a1 1 0 011-1h3.5a1 1 0 011 1c0 1.3.2 2.5.6 3.6a1 1 0 01-.3 1z"/></svg></span>1800 555 019</div>
<div class="abs contact-top" style="left:878px"><span class="ic"><svg width="14" height="14" viewBox="0 0 24 24"><rect x="3" y="6" width="18" height="12" fill="none" stroke="#fff" stroke-width="2"/><path d="M3 6l9 7 9-7" fill="none" stroke="#fff" stroke-width="2"/></svg></span>info@vemrilo.com</div>
<nav class="abs nav">
  <a class="active">HOME</a><a>MENU</a><a>RESERVATION</a><a>AWARDS</a><a>TESTIMONIALS</a><a>GALLERY</a><a>CONTACT</a>
</nav>
<div class="abs arrow" style="left:50px"><svg width="30" height="30"><path d="M18 9l-6 6 6 6" stroke="#fff" stroke-width="2" fill="none"/></svg></div>
<div class="abs arrow" style="left:1104px"><svg width="30" height="30"><path d="M12 9l6 6-6 6" stroke="#fff" stroke-width="2" fill="none"/></svg></div>
<h1 class="abs hero-title">Pakistani and Indian food</h1>
<div class="abs btn hero-btn">VIEW MENU</div>

<!-- welcome -->
<h2 class="abs section-title script" style="top:585px">Welcome!</h2>
<p class="abs section-sub" style="top:658px">WE OFFER FULL SERVICE PAKISTANI AND INDIAN FOOD</p>

<div class="abs feature" style="left:132px">
  <h3><svg width="34" height="26" viewBox="0 0 34 26"><rect x="1" y="4" width="20" height="14" fill="#2d6b0e"/><path d="M21 8h7l5 6v4H21z" fill="#2d6b0e"/><circle cx="8" cy="21" r="4" fill="#2d6b0e"/><circle cx="26" cy="21" r="4" fill="#2d6b0e"/></svg>Home Deliveries</h3>
  <p>Neque porro quisquam est, qui do-lorem ipsum quia dolor sit amet, consectetur, adipisci</p>
</div>
<div class="abs feature" style="left:451px">
  <h3><svg width="34" height="28" viewBox="0 0 34 28"><path d="M9 2h16v8a8 8 0 01-16 0z" fill="#2d6b0e"/><path d="M9 5H3a6 6 0 006 7M25 5h6a6 6 0 01-6 7" stroke="#2d6b0e" stroke-width="2" fill="none"/><rect x="15" y="17" width="4" height="6" fill="#2d6b0e"/><rect x="10" y="23" width="14" height="4" fill="#2d6b0e"/></svg>Award Winning</h3>
  <p>Neque porro quisquam est, qui do-lorem ipsum quia dolor sit amet, consectetur, adipisci</p>
</div>
<div class="abs feature" style="left:771px">
  <h3><svg width="34" height="32" viewBox="0 0 34 32"><rect x="2" y="4" width="30" height="26" fill="none" stroke="#2d6b0e" stroke-width="2.5"/><rect x="2" y="4" width="30" height="6" fill="#2d6b0e"/><path d="M2 17h30M2 24h30M10 10v20M17 10v20M24 10v20" stroke="#2d6b0e" stroke-width="1.5"/></svg>Reservations</h3>
  <p>Neque porro quisquam est, qui do-lorem ipsum quia dolor sit amet, consectetur, adipisci</p>
</div>

<!-- specials -->
<div class="abs specials"></div>
<h2 class="abs section-title script" style="top:972px;color:var(--white)">Specials</h2>
<p class="abs section-sub" style="top:1057px;color:#c8e0b0">SAFFRON LANE PROMISES YOU THE BEST DINING EXPERIENCE</p>

<div class="abs card" style="left:132px"><div class="photo" role="img" aria-label="Photo of biryani rice with grilled chicken" style="background:linear-gradient(135deg,#b8932a,#e0c050,#7a5a20)"></div><h4>Tikka Grove Delight Kebab</h4><div class="btn">View Detials</div></div>
<div class="abs card" style="left:372px"><div class="photo" role="img" aria-label="Photo of chicken with peppers and rice" style="background:linear-gradient(135deg,#8a2418,#c84a2a,#e8dcd0)"></div><h4>Tikka Grove Delight Kebab</h4><div class="btn">View Detials</div></div>
<div class="abs card" style="left:611px"><div class="photo" role="img" aria-label="Photo of curry with rice and salad" style="background:linear-gradient(135deg,#6a4a30,#c8a878,#e8e4d8)"></div><h4>Tikka Grove Delight Kebab</h4><div class="btn">View Detials</div></div>
<div class="abs card" style="left:850px"><div class="photo" role="img" aria-label="Photo of a curry dish with rice on a white plate" style="background:linear-gradient(135deg,#e8e4e0,#c89a50,#f0ede8)"></div><h4>Tikka Grove Delight Kebab</h4><div class="btn">View Detials</div></div>

<!-- testimonials -->
<h2 class="abs script" style="left:132px;top:1518px;font-size:50px;color:var(--red)">Testimonials</h2>
<p class="abs" style="left:132px;top:1588px;font-size:13px;letter-spacing:1.5px;color:var(--green)">SOME OF OUR HAPPY CUSTOMER'S REVIEWS</p>
<div class="abs quote-box"></div>
<div class="abs avatar" role="img" aria-label="Customer portrait"></div>
<div class="abs quote">
  <p><span style="font-size:44px;color:#aaa;line-height:10px;vertical-align:-14px;font-family:Georgia,serif">&#8220;</span> Neque porro quisquam est, qui dolorem ipsum quia dolor sit amet, consectetur, adipisci</p>
  <p style="margin-top:12px">Nemo enim ipsam voluptatem quia voluptas sit asper-natur aut odit aut fugit,</p>
  <p style="margin-top:12px;font-style:italic;color:var(--green)">- John Doe -</p>
  <p style="color:var(--red);font-size:12px;letter-spacing:1px;line-height:14px">★★★★★</p>
</div>

<!-- blog -->
<h2 class="abs script" style="left:624px;top:1518px;font-size:50px;color:var(--red)">Recent Blog</h2>
<p class="abs" style="left:624px;top:1588px;font-size:13px;letter-spacing:1.5px;color:var(--green)">SOME OF OUR CUSTOMER'S FAVOURITES</p>
<div class="abs post-photo" style="top:1640px;background:linear-gradient(135deg,#3a7a2a,#c83a2a,#e8e0d8)" role="img" aria-label="Photo of tandoori dish with salad"></div>
<div class="abs post" style="top:1634px"><h5>The Tandoor</h5><p class="date">Feb 02,2016</p><p>Neque porro quisquam est, qui dolorem ipsum quia dolor sit amet, consectetur</p></div>
<div class="abs post-photo" style="top:1783px;background:linear-gradient(135deg,#6a2a14,#a8481e,#5a2010)" role="img" aria-label="Photo of karahi curry"></div>
<div class="abs post" style="top:1778px"><h5>The Karahi</h5><p class="date">Feb 02,2016</p><p>Neque porro quisquam est, qui dolorem ipsum quia dolor sit amet, consectetur</p></div>

<!-- newsletter -->
<div class="abs newsletter"></div>
<h2 class="abs script" style="left:132px;top:1966px;font-size:48px;color:var(--white)">Newsletter</h2>
<p class="abs" style="left:134px;top:2035px;font-size:11px;letter-spacing:1px;color:var(--white)">SUBSCRIBE NEWSLETTER TO RECEIVE THE LATEST OFFERS DIRECT TO YOUR INBOX.</p>
<div class="abs mail-input"><svg width="14" height="12"><rect x="1" y="1" width="12" height="10" fill="none" stroke="#666"/><path d="M1 1l6 5 6-5" fill="none" stroke="#666"/></svg>ENTER YOUR MAIL ID</div>
<div class="abs subscribe">SUBSCRIBE</div>

<!-- footer -->
<div class="abs footer"></div>
<div class="abs fcol" style="left:132px;top:2128px"><h6>Quick Links</h6>
  <ul><li>Home</li><li>Menu</li><li>Reservation</li><li>Awards</li><li>Testimonials</li><li>Gallery</li><li>Contact</li></ul></div>
<div class="abs fcol" style="left:314px;top:2128px"><h6>Opening Hours</h6>
  <table class="hours"><tr><td>Monday</td><td>:</td><td>closed</td></tr><tr><td>Tue to Fri</td><td>:</td><td>11am to 9pm</td></tr><tr><td>Saturday</td><td>:</td><td>9am to 9pm</td></tr><tr><td>Sunday</td><td>:</td><td>9am to 12pm</td></tr></table></div>
<div class="abs fcol" style="left:538px;top:2128px;width:210px"><h6>Contact US</h6>
  <ul>
    <li class="ic"><svg width="10" height="13" viewBox="0 0 10 13"><path d="M5 0a5 5 0 00-5 5c0 4 5 8 5 8s5-4 5-8a5 5 0 00-5-5z" fill="#b9cfa8"/><circle cx="5" cy="5" r="2" fill="#1d4808"/></svg>Neque porro quisquam est, qui do-lorem ipsum quia dolor</li>
    <li class="ic" style="margin-top:18px"><svg width="11" height="11" viewBox="0 0 24 24"><path fill="#b9cfa8" d="M6.6 10.8a15 15 0 006.6 6.6l2.2-2.2a1 1 0 011-.3 11 11 0 003.6.6 1 1 0 011 1V20a1 1 0 01-1 1A17 17 0 013 4a1 1 0 011-1h3.5a1 1 0 011 1c0 1.3.2 2.5.6 3.6a1 1 0 01-.3 1z"/></svg>1800-555-019</li>
    <li class="ic"><svg width="12" height="10" viewBox="0 0 12 10"><rect x=".5" y=".5" width="11" height="9" fill="none" stroke="#b9cfa8"/><path d="M.5 .5l5.5 4.5 5.5-4.5" fill="none" stroke="#b9cfa8"/></svg>info@vemrilo.com</li>
  </ul></div>
<div class="abs footer-brand">Saffron Lane</div>
<div class="abs social" style="left:907px" aria-label="Share"><svg width="18" height="18" viewBox="0 0 18 18"><circle cx="4" cy="9" r="2.5" fill="#fff"/><circle cx="14" cy="4" r="2.5" fill="#fff"/><circle cx="14" cy="14" r="2.5" fill="#fff"/><path d="M4 9l10-5M4 9l10 5" stroke="#fff" stroke-width="1.5"/></svg></div>
<div class="abs social" style="left:963px" aria-label="Message"><svg width="18" height="18" viewBox="0 0 18 18"><path d="M2 3h14v9H7l-4 3v-3H2z" fill="#fff"/></svg></div>
<div class="abs social" style="left:1019px" aria-label="Link"><svg width="18" height="18" viewBox="0 0 18 18"><rect x="1.5" y="6" width="8" height="6" rx="3" fill="none" stroke="#fff" stroke-width="2"/><rect x="8.5" y="6" width="8" height="6" rx="3" fill="none" stroke="#fff" stroke-width="2"/></svg></div>
<div class="abs footer-bottom">© 2016 Saffron Lane, All Right Reserved.</div>

</body>
</html>
```